Moravel Aesthetic Doctor

I require an elegant, luxurious looking business card for my aesthetic business. I am a doctor and that will set me aside from competitors. I am planning to provide home and spa based treatments to clients with high expectations. I have attached my logo.

```html
<!DOCTYPE html>
<html lang="en">
<head>
<meta charset="utf-8">
<title>Moravel Aesthetic Doctor – Business Card</title>
<link href="https://fonts.googleapis.com/css2?family=Marcellus&family=Roboto:wght@400;700&display=swap" rel="stylesheet">
<style>
  :root {
    --stage: #3b3b3c;
    --card: #1d1d1f;
    --silver: #b9bbbe;
    --grey-text: #c9cacc;
    --blue: #3fa9e8;
    --blue-soft: #5bb8ef;
  }
  * { margin: 0; padding: 0; box-sizing: border-box; }
  html, body { width: 799px; height: 1200px; overflow: hidden; }
  body {
    background: var(--stage);
    font-family: 'Roboto', Arial, sans-serif;
    position: relative;
  }
  .card {
    position: absolute;
    left: 110px;
    width: 580px;
    height: 330px;
    background: var(--card);
    border-radius: 6px;
    box-shadow: 0 14px 30px rgba(0,0,0,0.45);
  }
  .card--front { top: 130px; }
  .card--back { top: 740px; }

  /* Front */
  .front-mark {
    position: absolute;
    left: 50%; top: 50%;
    transform: translate(-50%, -50%);
    display: flex;
    flex-direction: column;
    align-items: center;
    gap: 14px;
  }
  .front-mark__circle {
    width: 120px; height: 120px;
    border: 4px solid var(--silver);
    border-radius: 50%;
  }
  .front-mark__name {
    font-family: 'Marcellus', Georgia, serif;
    font-size: 22px;
    letter-spacing: 4px;
    color: var(--silver);
  }

  /* Back */
  .brand {
    position: absolute;
    left: 36px; top: 108px;
    display: flex;
    align-items: center;
    gap: 12px;
  }
  .brand__circle {
    width: 64px; height: 64px;
    border: 3px solid var(--silver);
    border-radius: 50%;
    flex: none;
  }
  .brand__name {
    font-family: 'Marcellus', Georgia, serif;
    color: var(--grey-text);
    line-height: 1;
  }
  .brand__name-main { display: block; font-size: 42px; letter-spacing: 2px; }
  .brand__name-sub { display: block; font-size: 16px; letter-spacing: 2.4px; margin-top: 4px; }

  .contact {
    position: absolute;
    left: 340px; top: 118px;
    color: var(--grey-text);
  }
  .contact__name {
    font-weight: 700;
    font-size: 17px;
    color: var(--grey-text);
  }
  .contact__post { font-weight: 400; font-size: 11px; color: var(--blue); margin-left: 4px; }
  .contact__role {
    font-size: 13px;
    line-height: 1.2;
    color: var(--blue);
    margin-top: 4px;
    margin-bottom: 12px;
  }
  .contact__line {
    display: flex;
    align-items: center;
    gap: 10px;
    font-size: 13.5px;
    margin-bottom: 5px;
  }
  .contact__line svg { width: 12px; height: 12px; flex: none; }
  .contact__social {
    display: flex;
    align-items: center;
    gap: 6px;
    font-size: 13.5px;
    margin-top: 2px;
  }
  .social-dot {
    width: 14px; height: 14px;
    border-radius: 50%;
    background: var(--blue-soft);
  }
</style>
</head>
<body>
  <section class="card card--front" aria-label="Card front">
    <div class="front-mark">
      <div class="front-mark__circle"></div>
      <div class="front-mark__name">Moravel</div>
    </div>
  </section>

  <section class="card card--back" aria-label="Card back">
    <div class="brand">
      <div class="brand__circle"></div>
      <div class="brand__name">
        <span class="brand__name-main">MORAVEL</span>
        <span class="brand__name-sub">AESTHETIC DOCTOR</span>
      </div>
    </div>

    <div class="contact">
      <div class="contact__name">Dr Elena Voss<span class="contact__post">MRCPCH MD</span></div>
      <div class="contact__role">Australasian Diploma<br>of Aesthetic Medicine</div>

      <div class="contact__line">
        <svg viewBox="0 0 24 24" fill="var(--blue)"><path d="M6.6 10.8a15 15 0 0 0 6.6 6.6l2.2-2.2c.3-.3.7-.4 1-.2 1.1.4 2.3.6 3.6.6.6 0 1 .4 1 1V20c0 .6-.4 1-1 1A17 17 0 0 1 3 4c0-.6.4-1 1-1h3.5c.6 0 1 .4 1 1 0 1.3.2 2.5.6 3.6.1.3 0 .7-.2 1z"/></svg>
        <span>0800 555 314</span>
      </div>
      <div class="contact__line">
        <svg viewBox="0 0 24 24" fill="var(--blue)"><path d="M2 5h20v14H2z" opacity=".9"/><path d="M2 5l10 8 10-8" stroke="#1d1d1f" stroke-width="2" fill="none"/></svg>
        <span>elena@moravel.co.nz</span>
      </div>
      <div class="contact__line">
        <svg viewBox="0 0 24 24" fill="none" stroke="var(--blue)" stroke-width="2"><circle cx="12" cy="12" r="10"/><path d="M2 12h20M12 2c3 3 3 17 0 20M12 2c-3 3-3 17 0 20"/></svg>
        <span>www.moravel.co.nz</span>
      </div>
      <div class="contact__social">
        <span>Follow us on:</span>
        <span class="social-dot"></span>
        <span class="social-dot"></span>
      </div>
    </div>
  </section>
</body>
</html>
```